Free range pig farm business

We'd like a simple but elegant website for our new free range pig farm business.
Check out www.kelvorrahogsteads.com.au and http://www.tirrowfield.com.au/
pages:
Home
About
Shop
Contact
Target Market(s)
People who would want to find out where they could buy our pork
Industry/Entity Type
Agribusiness
Number of Pages Required
4 page
Font styles to use
Other font styles liked:
- As per our logo
Requirements
Must have
- Ability for us to update weekly with new news and photos

```html
<!DOCTYPE html>
<html lang="en">
<head>
<meta charset="utf-8">
<title>Glenmarra Pastured Pork</title>
<link href="https://fonts.googleapis.com/css2?family=Cabin:wght@400;500;600;700&family=Open+Sans:wght@400;600&display=swap" rel="stylesheet">
<style>
:root{
  --paper:#e9e9e7;
  --paper-shade:#dfdfdc;
  --ink:#3a3a3a;
  --green-dark:#3c5a1f;
  --green-light:#9cbb2f;
  --muted:#8a8a88;
  --white:#ffffff;
}
*{box-sizing:border-box;margin:0;padding:0}
html,body{width:737px;height:1200px;overflow:hidden}
body{position:relative;font-family:"Open Sans",sans-serif;color:var(--ink);
  background:radial-gradient(circle at 30% 20%,#ececea 0%,var(--paper) 45%,var(--paper-shade) 100%)}
.abs{position:absolute}

/* rough torn edges for photo frames */
.torn-a{clip-path:polygon(0% 1%,4% 0%,9% 1.5%,15% 0%,22% 1%,30% 0%,38% 1.5%,46% 0%,55% 1%,63% 0%,71% 1.5%,79% 0%,86% 1%,93% 0%,100% 1%,99% 8%,100% 16%,98.5% 24%,100% 33%,99% 42%,100% 51%,98.5% 60%,100% 69%,99% 78%,100% 87%,99% 94%,100% 100%,93% 99%,86% 100%,78% 98.5%,70% 100%,62% 99%,54% 100%,46% 98.5%,38% 100%,30% 99%,22% 100%,14% 98.5%,7% 100%,0% 99%,1% 91%,0% 83%,1.5% 74%,0% 66%,1% 57%,0% 48%,1.5% 39%,0% 30%,1% 21%,0% 12%)}
.torn-b{clip-path:polygon(0% 0%,6% 1.5%,12% 0%,19% 2%,26% 0%,34% 1.5%,41% 0%,49% 2%,57% 0%,64% 1.5%,72% 0%,80% 2%,88% 0%,95% 1.5%,100% 0%,98% 9%,100% 18%,97.5% 28%,100% 38%,98% 48%,100% 58%,97.5% 68%,100% 78%,98% 88%,100% 100%,94% 98%,87% 100%,80% 97.5%,72% 100%,64% 98%,57% 100%,49% 97.5%,41% 100%,33% 98%,25% 100%,17% 97.5%,9% 100%,0% 98%,2% 89%,0% 79%,2.5% 69%,0% 59%,2% 49%,0% 39%,2.5% 29%,0% 19%,2% 9%)}
.grit{box-shadow:inset 0 0 18px rgba(0,0,0,.35)}

.social{left:80px;top:52px;display:flex;gap:14px}
.social span{width:20px;height:20px;border:1.5px solid var(--muted);border-radius:50%;display:block}
.brand{left:268px;top:18px;width:202px;text-align:center;font-family:"Cabin",sans-serif;color:var(--ink)}
.brand-mark{width:40px;height:40px;border-radius:50%;background:var(--green-dark);margin:0 auto 8px}
.brand-name{font-size:11px;font-weight:500;letter-spacing:.2px;line-height:13px}
.brand-sub{font-size:10px;font-weight:500;display:flex;align-items:center;justify-content:center;gap:6px;margin-top:1px}
.brand-sub::before,.brand-sub::after{content:"";width:22px;height:1px;background:var(--ink)}
.search{left:514px;top:51px;width:141px;height:26px;border:2px solid #a9a9a7;display:flex;align-items:center;justify-content:space-between;padding:0 7px 0 8px;font-size:6.5px;font-style:italic;color:#6f6f6d}
.nav{left:0;top:126px;width:737px;font-family:"Cabin",sans-serif;font-size:9px;font-weight:500;color:var(--ink)}
.nav a{position:absolute;transform:translateX(-50%);text-decoration:none;color:inherit;white-space:nowrap}
.nav a.active{color:var(--green-light)}

.hero{left:80px;top:162px;width:575px;height:270px;
  background:linear-gradient(180deg,#867a6c 0%,#8b8170 14%,#6f9448 26%,#7fa257 44%,#d8c2b6 60%,#cfb2a6 72%,#6b5642 86%,#54432f 100%)}
.hero-title{left:80px;top:266px;width:575px;text-align:center;font-family:"Cabin",sans-serif;font-weight:700;font-size:35px;color:var(--white);text-shadow:0 2px 4px rgba(0,0,0,.6)}
.dots{left:351px;top:405px;display:flex;gap:5px}
.dots span{width:7px;height:7px;border-radius:50%;background:rgba(255,255,255,.45)}
.dots span.on{background:var(--green-light)}

.card-img{top:454px;width:184px;height:123px}
.card{top:598px;width:186px}
.card h3{font-family:"Cabin",sans-serif;font-weight:600;font-size:12px;color:var(--green-dark);margin-bottom:7px}
.card p{font-size:5.5px;line-height:14.4px;color:var(--muted);text-align:justify;width:186px}
.more{display:inline-block;margin-top:8px;margin-left:2px;font-family:"Cabin",sans-serif;font-size:9px;color:var(--green-dark);text-decoration:underline}

.shop-title{left:0;top:723px;width:737px;text-align:center;font-family:"Cabin",sans-serif;font-weight:600;font-size:21px;letter-spacing:.3px;color:var(--ink)}
.product-img{top:782px;width:280px;height:140px}
.product{top:939px;width:290px;font-family:"Cabin",sans-serif}
.product h4{font-weight:600;font-size:12px;color:var(--green-dark);letter-spacing:.2px}
.price{font-family:"Open Sans",sans-serif;font-size:12px;margin-top:8px;color:var(--ink)}
.view{display:inline-block;margin-top:7px;font-size:8.5px;color:var(--green-dark);text-decoration:underline}

.newsletter{left:82px;top:1030px;width:573px;height:98px;background:linear-gradient(90deg,#2f2a27,#564843 30%,#6a5a55 55%,#4a403c 80%,#37312e)}
.news-head{left:130px;top:1060px;font-family:"Cabin",sans-serif;font-weight:600;font-size:21px;color:var(--white)}
.news-sub{left:130px;top:1094px;font-size:5.8px;color:#e6e6e6}
.news-input{left:392px;top:1066px;width:230px;height:31px;background:var(--white);display:flex;align-items:center;justify-content:space-between;padding:0 12px 0 11px;font-size:6px;color:#777}
.footer-nav{left:0;top:1150px;width:737px;text-align:center;font-family:"Cabin",sans-serif;font-size:7px;color:var(--ink)}
.footer-nav span{margin:0 6px}
.copyright{left:0;top:1171px;width:737px;text-align:center;font-size:5.8px;color:var(--ink)}
</style>
</head>
<body>

<div class="abs social" aria-label="Social links"><span></span><span></span><span></span></div>

<div class="abs brand">
  <div class="brand-mark"></div>
  <div class="brand-name">GLENMARRA PASTURED</div>
  <div class="brand-sub">PORK</div>
</div>

<div class="abs search">SEARCH...
  <svg width="9" height="9" viewBox="0 0 10 10"><circle cx="4" cy="4" r="3" fill="none" stroke="#3a3a3a" stroke-width="1.5"/><line x1="6.2" y1="6.2" x2="9" y2="9" stroke="#3a3a3a" stroke-width="1.6"/></svg>
</div>

<nav class="abs nav">
  <a class="active" style="left:217px">HOME</a>
  <a style="left:291px">ABOUT</a>
  <a style="left:367px">SERVICE</a>
  <a style="left:440px">SHOP</a>
  <a style="left:512px">CONTACT</a>
</nav>

<div class="abs hero torn-a grit" role="img" aria-label="Pigs resting on a grassy paddock in front of farm sheds and hay bales"></div>
<h1 class="abs hero-title">PIG FARM BUSINESS</h1>
<div class="abs dots"><span class="on"></span><span></span><span></span></div>

<div class="abs card-img torn-b grit" style="left:80px;background:linear-gradient(135deg,#8a5a44,#e3b0a0 40%,#f0c4b6 60%,#9c6450)" role="img" aria-label="Young pigs huddled together in a pen"></div>
<div class="abs card-img torn-a grit" style="left:276px;background:linear-gradient(135deg,#c8504e,#f0a29c 45%,#e88a84 65%,#b8443e)" role="img" aria-label="Raw pork ribs"></div>
<div class="abs card-img torn-b grit" style="left:471px;background:linear-gradient(180deg,#2f4a2a,#5d7e3e 35%,#86a85c 65%,#6b8a48)" role="img" aria-label="Pig standing on a green pasture"></div>

<div class="abs card" style="left:80px">
  <h3>THE PIGS</h3>
  <p>Nemo enim ipsam voluptatem quia voluptas sit aspernatur aut odit aut fugit, sed quia consequuntur magni dolores eos qui ratione voluptatem sequi nesciunt.</p>
  <a class="more">MORE ›</a>
</div>
<div class="abs card" style="left:276px">
  <h3>THE PORK</h3>
  <p>Nemo enim ipsam voluptatem quia voluptas sit aspernatur aut odit aut fugit, sed quia consequuntur magni dolores eos qui ratione voluptatem sequi nesciunt.</p>
  <a class="more">MORE ›</a>
</div>
<div class="abs card" style="left:471px">
  <h3>ABOUT PASTURED</h3>
  <p>Nemo enim ipsam voluptatem quia voluptas sit aspernatur aut odit aut fugit, sed quia consequuntur magni dolores eos qui ratione voluptatem sequi nesciunt.</p>
  <a class="more">MORE ›</a>
</div>

<h2 class="abs shop-title">OUR FARM SHOP</h2>

<div class="abs product-img torn-a grit" style="left:80px;background:linear-gradient(135deg,#3a2c24,#6a5242 45%,#5a4436 70%,#33271f)" role="img" aria-label="Sliced grilled steak on a fork over a wooden board"></div>
<div class="abs product-img torn-b grit" style="left:376px;background:linear-gradient(135deg,#4a2e1a,#a8764e 45%,#c89a70 60%,#6a3e20)" role="img" aria-label="Grilled pork chop topped with herbs"></div>

<div class="abs product" style="left:80px">
  <h4>PORK CHOPS WITH CHIVE AND CREAM</h4>
  <div class="price">$50.00</div>
  <a class="view">VIEW PRODUCT ›</a>
</div>
<div class="abs product" style="left:377px">
  <h4>PORK CHOPS WITH CHIVE AND CREAM</h4>
  <div class="price">$50.00</div>
  <a class="view">VIEW PRODUCT ›</a>
</div>

<div class="abs newsletter torn-b grit" role="img" aria-label="Dark background photo of pigs in a pen"></div>
<h2 class="abs news-head">NEWSLETTER</h2>
<p class="abs news-sub">Subscribe newsletter to receive the latest news and updates direct to your inbox.</p>
<div class="abs news-input">Enter Your Email Address
  <svg width="12" height="12" viewBox="0 0 12 12"><path d="M11 1 L1 5.5 L4.5 7 L5.5 11 Z" fill="#111"/></svg>
</div>

<div class="abs footer-nav">HOME<span>|</span>ABOUT<span>|</span>SERVICE<span>|</span>SHOP<span>|</span>CONTACT</div>
<div class="abs copyright">2016 © GLENMARRA PORK. ALL RIGHT RESERVED.</div>

</body>
</html>
```